Retractable banner.
Health Check For Pets
Check for Ear Mites
Skin Health
Fleas & Ticks

A space SERVE BY <NAME OF CLINIC>

Ideally contain pictures of cats and dogs

```html
<!DOCTYPE html>
<html lang="en">
<head>
<meta charset="utf-8">
<title>Health Check for Pets – Banner</title>
<link href="https://fonts.googleapis.com/css2?family=Montserrat:wght@700;800;900&display=swap" rel="stylesheet">
<style>
  :root {
    --page-bg: #e9eaec;
    --banner-bg: #fbfaf7;
    --brand-red: #a8161a;
    --ink: #1b1b1b;
    --white: #ffffff;
    --logo-grey: #d6d6d6;
    --logo-text: #9a9a9a;
    --tick-dark: #3b3b3b;
    --tick-sand: #e6c98e;
    --dog-brown: #b0521f;
    --dog-cream: #f3e6d2;
  }
  * { box-sizing: border-box; margin: 0; padding: 0; }
  html, body {
    width: 1200px; height: 825px; overflow: hidden;
    background: var(--page-bg);
    font-family: "Montserrat", Arial, sans-serif;
  }
  .banner {
    position: absolute; left: 50px; top: 132px;
    width: 1100px; height: 560px;
    background: var(--banner-bg);
    box-shadow: 0 6px 24px rgba(0,0,0,.12);
    overflow: hidden;
  }
  .logo-spot {
    position: absolute; left: 880px; top: 22px;
    width: 175px; height: 130px; border-radius: 50%;
    background: var(--logo-grey);
    display: flex; align-items: center; justify-content: center;
    text-align: center; color: var(--logo-text);
    font-weight: 800; font-size: 28px; line-height: .95;
  }
  .kicker {
    position: absolute; left: 52px; top: 150px;
    color: var(--brand-red); font-weight: 800; font-size: 29px;
    text-transform: uppercase; letter-spacing: .5px;
  }
  .headline {
    position: absolute; left: 44px; top: 178px;
    color: var(--ink); font-weight: 900; font-size: 132px; line-height: 1;
    letter-spacing: -2px;
  }
  .check-band {
    position: absolute; left: 0; top: 310px;
    width: 590px; height: 160px;
    background: var(--brand-red);
    clip-path: polygon(0 0, 100% 0, 82% 100%, 0 100%);
    padding: 14px 0 0 40px;
    color: var(--white); font-weight: 800; font-size: 27px;
    text-transform: uppercase; line-height: 1.22;
  }
  .check-list { list-style: none; }
  .check-list li { display: flex; align-items: center; gap: 10px; }
  .check-list svg { width: 22px; height: 22px; flex: none; }
  .serve-by {
    position: absolute; left: 40px; top: 478px; width: 560px;
    display: flex; align-items: center; gap: 12px;
    font-weight: 800; font-size: 18px; color: var(--ink);
  }
  .serve-by .rule { flex: 1; height: 3px; background: var(--ink); }
  .clinic-name {
    position: absolute; left: 40px; top: 502px;
    color: var(--brand-red); font-weight: 800; font-size: 38px;
  }
  .magnify {
    position: absolute; left: 500px; top: 92px;
    width: 250px; height: 250px; border-radius: 50%;
    border: 9px solid var(--brand-red);
    background: radial-gradient(circle at 50% 60%, var(--tick-sand) 0 30%, var(--tick-dark) 75%);
  }
  .pointer { position: absolute; left: 740px; top: 220px; width: 110px; height: 60px; }
  .dog-art {
    position: absolute; left: 850px; top: 170px;
    width: 230px; height: 290px; border-radius: 40px;
    background: linear-gradient(160deg, var(--dog-brown) 0 45%, var(--dog-cream) 100%);
  }
</style>
</head>
<body>
  <main class="banner">
    <div class="logo-spot">your<br>logo<br>here</div>

    <p class="kicker">Health Check For</p>
    <h1 class="headline">PETS</h1>

    <section class="check-band">
      <ul class="check-list">
        <li>Check For</li>
        <li><svg viewBox="0 0 24 24"><circle cx="12" cy="12" r="10" fill="none" stroke="#fff" stroke-width="2"/><path d="M7 12.5l3.2 3.2L17 9" fill="none" stroke="#fff" stroke-width="2.4"/></svg>Ear Mites</li>
        <li><svg viewBox="0 0 24 24"><circle cx="12" cy="12" r="10" fill="none" stroke="#fff" stroke-width="2"/><path d="M7 12.5l3.2 3.2L17 9" fill="none" stroke="#fff" stroke-width="2.4"/></svg>Skin Health</li>
        <li><svg viewBox="0 0 24 24"><circle cx="12" cy="12" r="10" fill="none" stroke="#fff" stroke-width="2"/><path d="M7 12.5l3.2 3.2L17 9" fill="none" stroke="#fff" stroke-width="2.4"/></svg>Fleas &amp; Ticks</li>
      </ul>
    </section>

    <div class="serve-by"><span class="rule"></span><span>SERVE BY:</span><span class="rule"></span></div>
    <p class="clinic-name">Pet Health Care CLINIC</p>

    <div class="magnify" role="img" aria-label="Magnified cartoon tick crawling among pet hair"></div>
    <svg class="pointer" viewBox="0 0 110 60" aria-hidden="true">
      <path d="M2 8 Q50 40 90 36" fill="none" stroke="var(--brand-red)" stroke-width="6"/>
      <path d="M84 22 L108 36 L84 50 Z" fill="var(--brand-red)"/>
    </svg>
    <div class="dog-art" role="img" aria-label="Cartoon beagle puppy scratching itself while sitting on a mat"></div>
  </main>
</body>
</html>
```